Business card for medical clinic

I need an upmarket, modern medical/health business card for my clinic

Contact Information for Business Card

name, address, email, qr code

```html
<!DOCTYPE html>
<html lang="en">
<head>
<meta charset="utf-8">
<title>Meridian Care Partners – Business Card</title>
<link rel="stylesheet" href="https://fonts.googleapis.com/css2?family=Poppins:wght@300;400;600&display=swap">
<style>
  :root {
    --stage: #1f1f20;
    --card-dark: #232326;
    --brand-blue: #22aae2;
    --brand-blue-deep: #1683bd;
    --ink-light: #ffffff;
    --ink-soft: #dfe6ea;
  }
  html, body {
    margin: 0;
    padding: 0;
    width: 1200px;
    height: 780px;
    overflow: hidden;
    background: var(--stage);
    font-family: "Poppins", sans-serif;
  }
  .canvas {
    position: relative;
    width: 1200px;
    height: 780px;
  }
  .card {
    position: absolute;
    top: 241px;
    width: 520px;
    height: 297px;
    overflow: hidden;
    box-shadow: 0 14px 30px rgba(0,0,0,0.45);
  }
  .card-front { left: 60px; background: var(--card-dark); }
  .card-back  { left: 620px; background: var(--brand-blue); }

  .swoosh { position: absolute; inset: 0; }

  .person {
    position: absolute;
    left: 58px;
    top: 36px;
  }
  .person-name {
    margin: 0;
    font-size: 27px;
    line-height: 1.1;
    color: var(--brand-blue);
    font-weight: 300;
    letter-spacing: 0.3px;
  }
  .person-name .first { font-weight: 600; }
  .person-role {
    margin: 4px 0 0 58px;
    font-size: 12px;
    color: var(--ink-light);
    font-weight: 400;
  }

  .brand-mark {
    position: absolute;
    display: flex;
    align-items: center;
    gap: 10px;
  }
  .card-front .brand-mark { left: 290px; top: 52px; }
  .brand-ring {
    border-radius: 50%;
    border: 2px solid currentColor;
    flex: none;
  }
  .brand-name {
    margin: 0;
    font-weight: 400;
    text-transform: uppercase;
    line-height: 1.15;
  }
  .card-front .brand-mark { color: var(--brand-blue); }
  .card-front .brand-ring { width: 34px; height: 34px; }
  .card-front .brand-name { font-size: 14px; letter-spacing: 1.6px; }

  .divider {
    position: absolute;
    left: 248px;
    top: 128px;
    width: 1px;
    height: 72px;
    background: var(--brand-blue);
  }

  .contact-list {
    position: absolute;
    left: 268px;
    top: 126px;
    margin: 0;
    padding: 0;
    list-style: none;
  }
  .contact-item {
    display: flex;
    align-items: center;
    gap: 9px;
    height: 24px;
    font-size: 13.5px;
    color: var(--ink-soft);
    font-weight: 400;
  }
  .contact-icon { width: 13px; height: 13px; flex: none; }

  .address {
    position: absolute;
    left: 40px;
    top: 252px;
    margin: 0;
    font-size: 13px;
    color: var(--ink-light);
    font-weight: 400;
    letter-spacing: 0.2px;
  }

  .card-back .brand-mark {
    left: 50%;
    top: 50%;
    transform: translate(-50%, -50%);
    color: var(--ink-light);
    gap: 16px;
  }
  .card-back .brand-ring { width: 64px; height: 64px; border-width: 3px; }
  .card-back .brand-name { font-size: 25px; letter-spacing: 2.5px; }
</style>
</head>
<body>
<main class="canvas">

  <section class="card card-front" aria-label="Business card front">
    <svg class="swoosh" width="520" height="297" viewBox="0 0 520 297" aria-hidden="true">
      <defs>
        <linearGradient id="band-fill" x1="0" y1="0" x2="1" y2="0">
          <stop offset="0" stop-color="#e9f2f8"/>
          <stop offset="0.12" stop-color="#2aa6de"/>
          <stop offset="0.55" stop-color="#1c8fca"/>
          <stop offset="0.88" stop-color="#1a7fb6"/>
          <stop offset="1" stop-color="#e9f2f8"/>
        </linearGradient>
      </defs>
      <path d="M0,118 C110,205 300,238 520,236 L520,297 L0,297 Z" fill="url(#band-fill)"/>
      <path d="M28,110 C140,200 320,222 500,226" fill="none" stroke="#121214" stroke-width="5"/>
      <path d="M40,104 C150,188 320,212 505,216" fill="none" stroke="var(--brand-blue)" stroke-width="1.6"/>
    </svg>

    <div class="person">
      <h1 class="person-name"><span class="first">Lena</span> Marlow</h1>
      <p class="person-role">Founder &amp; CEO</p>
    </div>

    <div class="brand-mark">
      <span class="brand-ring"></span>
      <p class="brand-name">Meridian Care<br>Partners</p>
    </div>

    <span class="divider"></span>

    <ul class="contact-list">
      <li class="contact-item">
        <svg class="contact-icon" viewBox="0 0 16 16" aria-hidden="true"><path d="M3.5 1.5l2.5 0.5 1 3-1.8 1.3c0.8 1.8 2 3 3.8 3.8L10.3 8.3l3 1 0.5 2.5-2 2C6.5 13.5 2.5 9.5 1.5 3.5z" fill="var(--brand-blue)"/></svg>
        (555) 204-1187
      </li>
      <li class="contact-item">
        <svg class="contact-icon" viewBox="0 0 16 16" aria-hidden="true"><rect x="1" y="3" width="14" height="10" rx="1.5" fill="none" stroke="var(--brand-blue)" stroke-width="1.6"/><path d="M1.5 4l6.5 5 6.5-5" fill="none" stroke="var(--brand-blue)" stroke-width="1.6"/></svg>
        hello@meridiancare.com
      </li>
      <li class="contact-item">
        <svg class="contact-icon" viewBox="0 0 16 16" aria-hidden="true"><circle cx="8" cy="8" r="6.5" fill="none" stroke="var(--brand-blue)" stroke-width="1.5"/><ellipse cx="8" cy="8" rx="2.8" ry="6.5" fill="none" stroke="var(--brand-blue)" stroke-width="1.2"/><path d="M1.5 8h13" stroke="var(--brand-blue)" stroke-width="1.2"/></svg>
        www.meridiancare.com
      </li>
    </ul>

    <p class="address">418 Linden Ave. Suite 120 Dallas, TX 75201</p>
  </section>

  <section class="card card-back" aria-label="Business card back">
    <div class="brand-mark">
      <span class="brand-ring"></span>
      <p class="brand-name">Meridian Care<br>Partners</p>
    </div>
  </section>

</main>
</body>
</html>
```